Website for International Non-Profit for Birth Parent Searching

LumaKin is a 501(c)(3) non-profit organization that helps Chinese adoptees search and reunite with birth families who were separated due the One Child Policy in China. We want to create a website that can link to an information database that allows website users to easily access information around search ads in an organized way; help connect families to professional searchers; provide resources for community support for adoptees and their families as they embark on a personal and emotional journey of finding birth family through support groups on social media and consultation/education on the searching process; and provide the opportunity for the adoptive community to give back through donations and volunteer opportunities. The final design should foster a sense of community and be easy navigable to access the multiple resources we provide to help families search for each other. We would like to see designs with red/black/white color schemes that are gentle, inviting, and family friendly to viewers. We would like to see some design layouts with Chinese themes, if possible.

```html
<!DOCTYPE html>
<html lang="en">
<head>
<meta charset="utf-8">
<title>LumaKin – Find Your Birth Family</title>
<link href="https://fonts.googleapis.com/css2?family=Montserrat:wght@600;700;800&family=Roboto:wght@400;500;700&display=swap" rel="stylesheet">
<style>
:root{
  --red:#b5121b;
  --red-deep:#a30f17;
  --ink:#111111;
  --text:#333333;
  --muted:#555555;
  --blush:#f6dfe0;
  --white:#ffffff;
  --footer:#0b0b0b;
  --line:#cfcfcf;
}
*{box-sizing:border-box;margin:0;padding:0}
html,body{width:1200px;height:4451px;overflow:hidden}
body{font-family:Roboto,Arial,sans-serif;color:var(--text);background:var(--white);position:relative}
.accent{color:var(--red)}
.btn{position:absolute;display:flex;align-items:center;justify-content:center;background:var(--red);color:var(--white);font-family:Roboto,Arial,sans-serif;font-weight:700;font-size:16px;border-radius:30px;box-shadow:0 4px 8px rgba(0,0,0,.25);text-transform:uppercase}
section,header,footer{position:absolute;left:0;width:1200px}
.photo{position:absolute}

/* header */
.site-header{top:0;height:121px;border-top:6px solid var(--red);background:var(--white)}
.brand{position:absolute;left:108px;top:24px;display:flex;align-items:center;gap:10px}
.brand-dot{width:26px;height:26px;border-radius:50%;background:var(--red)}
.brand-name{font-family:Montserrat,Arial,sans-serif;font-weight:800;font-size:30px;color:var(--ink)}
.callbar{position:absolute;left:590px;top:28px;font-size:14px;font-weight:500;color:var(--ink);display:flex;align-items:center;gap:12px}
.social-dot{width:10px;height:10px;border-radius:50%;background:var(--ink);display:inline-block}
.login{left:930px;top:17px;width:158px;height:38px;border-radius:3px;font-size:14px;text-transform:none;box-shadow:none}
.nav{position:absolute;left:624px;top:76px;display:flex;gap:28px;font-size:14px;font-weight:500;color:var(--ink)}
.nav .active{color:var(--red);position:relative}
.nav .active::after{content:"";position:absolute;left:0;right:0;bottom:-12px;height:3px;background:var(--red)}

/* hero */
.hero{top:121px;height:600px;background:linear-gradient(100deg,#3a5a2a 0%,#6f8c4a 40%,#a9b98a 65%,#5f7f3f 100%)}
.hero h1{position:absolute;left:108px;top:124px;font-family:Montserrat,Arial,sans-serif;font-weight:800;font-size:47px;line-height:62px;letter-spacing:-0.5px;color:var(--white);text-transform:uppercase;white-space:nowrap}
.hero p{position:absolute;left:110px;top:318px;width:470px;color:var(--white);font-size:15px;line-height:29px;font-weight:500}
.hero .btn{left:110px;top:410px;width:202px;height:56px}
.arrow{position:absolute;top:279px;width:42px;height:42px;border-radius:50%;background:var(--red);display:flex;align-items:center;justify-content:center}
.arrow.prev{left:30px}.arrow.next{left:1083px}

/* welcome */
.welcome{top:721px;height:527px;text-align:center}
.section-title{font-family:Montserrat,Arial,sans-serif;font-weight:800;font-size:34px;color:var(--ink);text-transform:uppercase}
.welcome .section-title{margin-top:86px}
.welcome p{width:900px;margin:32px auto 0;font-size:13px;line-height:30px;color:var(--text)}
.welcome .btn{left:500px;top:377px;width:200px;height:54px}

/* organized */
.organized{top:1248px;height:552px;background:var(--blush)}
.organized .photo{left:0;top:0;width:600px;height:552px;background:linear-gradient(135deg,#c9b9a6,#7b6a5c 55%,#3e3530)}
.organized .section-title{position:absolute;left:645px;top:84px}
.organized .title-rule{position:absolute;left:645px;top:134px;width:60px;height:3px;background:var(--red)}
.org-list{position:absolute;left:648px;top:168px;width:510px;list-style:none;font-size:14px;line-height:39px;color:var(--text)}
.org-list li{position:relative;padding-left:28px}
.org-list li svg{position:absolute;left:0;top:13px}

/* team */
.team{top:1800px;height:742px;background:radial-gradient(ellipse at 30% 20%,#c4242b 0%,#b3141c 45%,#a30f17 100%)}
.team .section-title{color:var(--white);text-align:center;margin-top:88px}
.team .title-rule{width:70px;height:3px;background:var(--white);margin:12px auto 0}
.member{position:absolute;width:474px;height:195px;background:var(--white);box-shadow:0 3px 10px rgba(0,0,0,.2)}
.member .photo{left:0;top:0;width:190px;height:195px}
.member .info{position:absolute;left:205px;top:18px;width:255px}
.member h3{font-family:Montserrat,Arial,sans-serif;font-weight:700;font-size:16px;color:var(--red);text-transform:uppercase}
.member .role{font-size:11px;font-weight:500;color:var(--ink);margin-top:8px;text-transform:uppercase}
.member p{font-size:12px;line-height:24px;color:var(--muted);margin-top:10px}
.member .meta{display:flex;justify-content:space-between;align-items:center;margin-top:6px;font-size:10px;font-weight:700;color:#999}
.member .dots{display:flex;gap:6px}
.member .dots span{width:8px;height:8px;border-radius:50%;background:var(--red)}

/* blogs */
.blogs{top:2542px;height:927px}
.blogs .section-title{text-align:center;margin-top:86px}
.blogs .title-rule{width:62px;height:3px;background:var(--red);margin:12px auto 0}
.blogs .lede{width:940px;margin:28px auto 0;text-align:center;font-size:14px;line-height:30px;text-transform:uppercase;color:var(--text)}
.feature-photo{left:97px;top:259px;width:479px;height:312px;background:linear-gradient(160deg,#8fae7a,#c8c0b2 50%,#4f6b3a)}
.feature h3{position:absolute;left:105px;top:594px;width:440px;font-family:Montserrat,Arial,sans-serif;font-weight:700;font-size:21px;line-height:29px;color:var(--ink)}
.feature p{position:absolute;left:105px;top:665px;width:460px;font-size:14px;line-height:30px}
.feature .btn{left:78px;top:747px;width:174px;height:46px;font-size:15px}
.post{position:absolute;left:588px;width:520px;height:173px}
.post .photo{left:0;top:0;width:181px;height:173px}
.post h4{position:absolute;left:200px;top:4px;width:310px;font-family:Montserrat,Arial,sans-serif;font-weight:700;font-size:15px;line-height:30px;color:var(--ink);text-transform:uppercase}
.post p{position:absolute;left:200px;top:68px;width:300px;font-size:14px;line-height:30px;color:var(--muted)}

/* contact */
.contact{top:3469px;height:691px;background:var(--blush)}
.contact .section-title{text-align:center;margin-top:90px}
.field{position:absolute;background:var(--white);border:1px solid var(--line);box-shadow:0 2px 4px rgba(0,0,0,.12);font-size:12px;color:#444;padding:17px 18px}
.contact .btn{left:524px;top:541px;width:166px;height:40px;font-size:14px}

/* footer */
.site-footer{top:4160px;height:291px;background:var(--footer);color:var(--white)}
.footer-brand{position:absolute;left:145px;top:162px;display:flex;align-items:center;gap:10px}
.footer-brand .brand-name{color:var(--white);font-size:34px}
.footer-nav{position:absolute;left:392px;top:96px;display:flex;gap:28px;font-size:13px;font-weight:700}
.footer-rule{position:absolute;left:362px;top:136px;width:726px;height:1px;background:#777}
.contacts{position:absolute;left:418px;top:165px;display:flex;gap:40px;font-size:12px;align-items:center}
.contacts div{display:flex;align-items:center;gap:14px}
.ico{width:28px;height:28px;background:var(--white);border-radius:2px;display:flex;align-items:center;justify-content:center}
.copyright{position:absolute;left:425px;top:246px;font-size:11px;font-weight:500}
</style>
</head>
<body>

<header class="site-header">
  <div class="brand"><span class="brand-dot"></span><span class="brand-name">LumaKin</span></div>
  <div class="callbar">Call Now: 123 456 7890 <span class="social-dot"></span><span class="social-dot"></span><span class="social-dot"></span><span class="social-dot"></span></div>
  <div class="btn login">Member Login</div>
  <nav class="nav"><span class="active">Home</span><span>About Us</span><span>Services</span><span>Reviews</span><span>Blogs</span><span>Contact Us</span></nav>
</header>

<section class="hero" role="img" aria-label="A smiling girl running across a park lawn with her parents behind her">
  <h1>Find your birth<br>parents and your<br>birth family</h1>
  <p>Lorem ipsum dolor sit amet, consectetur adipiscing elit, sed do eiusmod tempor incididunt ut labore et dolore .</p>
  <div class="btn">Get Started</div>
  <div class="arrow prev"><svg width="14" height="14" viewBox="0 0 14 14"><path d="M9 2 4 7l5 5" stroke="#fff" stroke-width="2" fill="none"/></svg></div>
  <div class="arrow next"><svg width="14" height="14" viewBox="0 0 14 14"><path d="M5 2l5 5-5 5" stroke="#fff" stroke-width="2" fill="none"/></svg></div>
</section>

<section class="welcome">
  <h2 class="section-title">Welcome <span class="accent">to LumaKin</span></h2>
  <p>Lorem ipsum dolor sit amet, consectetur adipiscing elit, sed do eiusmod tempor incididunt ut labore et dolore magna aliqua. Ut enim ad minim veniam, quis nostrud exercitation ullamco laboris nisi ut aliquip ex ea commodo consequat. Duis aute irure dolor in reprehenderit in voluptate velit esse cillum dolore eu fugiat nulla pariatur. Excepteur sint occaecat cupidatat non proident, sunt in culpa qui officia deserunt mollit anim id est laborumexercitation ullamco laboris nisi ut aliquip ex ea commodo consequat. Duis aute irure dolor in reprehenderit in voluptate velit esse cillum dolore eu fugiat nulla pariatur. Excepteur sint occaecat cupidatat non proident, sunt in culpa qui officia deserunt mollit anim id est laborum. Excepteur sint occaecat cupidatat non proident, sunt in culpa qui officia deserunt mollit anim id.</p>
  <div class="btn">Learn More</div>
</section>

<section class="organized">
  <div class="photo" role="img" aria-label="Three generations of a family sitting together on a sofa"></div>
  <h2 class="section-title">Our <span class="accent">Organized Way</span></h2>
  <div class="title-rule"></div>
  <ul class="org-list">
    <li><svg width="14" height="14" viewBox="0 0 14 14"><circle cx="7" cy="7" r="7" fill="#b5121b"/><path d="M4 7.2l2 2 4-4" stroke="#fff" stroke-width="1.8" fill="none"/></svg>help connect families to professional searchers</li>
    <li><svg width="14" height="14" viewBox="0 0 14 14"><circle cx="7" cy="7" r="7" fill="#b5121b"/><path d="M4 7.2l2 2 4-4" stroke="#fff" stroke-width="1.8" fill="none"/></svg>provide resources for community support for adoptees and their families as they embark on a personal and emotional journey of finding birth family through support groups on social media and consultation/education on the searching process</li>
    <li><svg width="14" height="14" viewBox="0 0 14 14"><circle cx="7" cy="7" r="7" fill="#b5121b"/><path d="M4 7.2l2 2 4-4" stroke="#fff" stroke-width="1.8" fill="none"/></svg>and provide the opportunity for the adoptive community to give back through donations and volunteer opportunities.</li>
  </ul>
</section>

<section class="team">
  <h2 class="section-title">Meet Our Team</h2>
  <div class="title-rule"></div>

  <article class="member" style="left:107px;top:206px">
    <div class="photo" role="img" aria-label="Portrait of Elizabeth" style="background:linear-gradient(135deg,#eeeeee,#c9c2bc)"></div>
    <div class="info"><h3>Elizabeth</h3><div class="role">CEO in Company</div><p>Lorem ipsum dolor sit amet, consectetur adipiscing elit, sed do eiusmod tempor incididunt ut labore et.</p><div class="meta"><span class="dots"><span></span><span></span><span></span><span></span></span><span>15 COMMENT</span></div></div>
  </article>
  <article class="member" style="left:609px;top:206px">
    <div class="photo" role="img" aria-label="Portrait of John Doe" style="background:linear-gradient(135deg,#9fb3c4,#3c4a59)"></div>
    <div class="info"><h3>John Doe</h3><div class="role">CEO in Company</div><p>Lorem ipsum dolor sit amet, consectetur adipiscing elit, sed do eiusmod tempor incididunt ut labore et.</p><div class="meta"><span class="dots"><span></span><span></span><span></span><span></span></span><span>15 COMMENT</span></div></div>
  </article>
  <article class="member" style="left:107px;top:434px">
    <div class="photo" role="img" aria-label="Portrait of Alex Doe" style="background:linear-gradient(135deg,#e4e4e4,#56688a)"></div>
    <div class="info"><h3>Alex Doe</h3><div class="role">CEO in Company</div><p>Lorem ipsum dolor sit amet, consectetur adipiscing elit, sed do eiusmod tempor incididunt ut labore et.</p><div class="meta"><span class="dots"><span></span><span></span><span></span><span></span></span><span>15 COMMENT</span></div></div>
  </article>
  <article class="member" style="left:609px;top:434px">
    <div class="photo" role="img" aria-label="Portrait of Victoria" style="background:linear-gradient(135deg,#eeeeee,#7c7c80)"></div>
    <div class="info"><h3>Victoria</h3><div class="role">CEO in Company</div><p>Lorem ipsum dolor sit amet, consectetur adipiscing elit, sed do eiusmod tempor incididunt ut labore et.</p><div class="meta"><span class="dots"><span></span><span></span><span></span><span></span></span><span>15 COMMENT</span></div></div>
  </article>
</section>

<section class="blogs">
  <h2 class="section-title">Our <span class="accent">Latest Blogs</span></h2>
  <div class="title-rule"></div>
  <p class="lede">Lorem ipsum dolor sit amet, consectetur adipiscing elit, sed do eiusmod tempor incididunt ut labore et dolore<br>magna aliqua. Ut enim ad minim veniam, quis nostrud exercitation ullamco laboris</p>

  <div class="feature">
    <div class="photo feature-photo" role="img" aria-label="Parents walking with their child outside a house"></div>
    <h3>Lorem ipsum dolor sit amet, cons ectetur adipiscing elit.</h3>
    <p>Lorem ipsum dolor sit amet, consectetur adipiscing elit, sed do eiusmod tempor incididunt ut labore et magna aliqua.</p>
    <div class="btn">Learn More</div>
  </div>

  <article class="post" style="top:259px">
    <div class="photo" role="img" aria-label="Mother carrying her daughter piggyback outdoors" style="background:linear-gradient(135deg,#8dbb6a,#3f6e2e)"></div>
    <h4>Lorem ipsum dolor sit amet, consectetur adipisc.</h4>
    <p>Lorem ipsum dolor sit amet, consectetur aipiscing elit, sed do eiusmod tempor incid</p>
  </article>
  <article class="post" style="top:444px">
    <div class="photo" role="img" aria-label="Mother hugging her daughter closely" style="background:linear-gradient(135deg,#b08d72,#4a3328)"></div>
    <h4>Lorem ipsum dolor sit amet, consectetur adipisc.</h4>
    <p>Lorem ipsum dolor sit amet, consectetur aipiscing elit, sed do eiusmod tempor incid</p>
  </article>
  <article class="post" style="top:629px">
    <div class="photo" role="img" aria-label="Grandmother embracing a young girl in a garden" style="background:linear-gradient(135deg,#7fa85c,#c8b9a8)"></div>
    <h4>Lorem ipsum dolor sit amet, consectetur adipisc.</h4>
    <p>Lorem ipsum dolor sit amet, consectetur aipiscing elit, sed do eiusmod tempor incid</p>
  </article>
</section>

<section class="contact">
  <h2 class="section-title">Get <span class="accent">in Touch</span></h2>
  <div class="field" style="left:207px;top:188px;width:395px;height:48px">First Name</div>
  <div class="field" style="left:612px;top:188px;width:393px;height:48px">Last Name</div>
  <div class="field" style="left:207px;top:248px;width:395px;height:48px">Email address</div>
  <div class="field" style="left:612px;top:248px;width:393px;height:48px">Address</div>
  <div class="field" style="left:207px;top:309px;width:798px;height:60px">Phone number</div>
  <div class="field" style="left:207px;top:385px;width:798px;height:121px">Reason for Inquiry</div>
  <div class="btn">Submit</div>
</section>

<footer class="site-footer">
  <div class="footer-brand"><span class="brand-dot"></span><span class="brand-name">LumaKin</span></div>
  <nav class="footer-nav"><span>HOME</span><span>ABOUT US</span><span>SERVICES</span><span>REVIEWS</span><span>BLOGS</span><span>CONTACT US</span></nav>
  <div class="footer-rule"></div>
  <div class="contacts">
    <div><span class="ico"><svg width="16" height="16" viewBox="0 0 16 16"><path d="M3 1h3l1.5 4-2 1.3a9 9 0 0 0 4.2 4.2L11 8.5 15 10v3a2 2 0 0 1-2 2A12 12 0 0 1 1 3a2 2 0 0 1 2-2z" fill="#b5121b"/></svg></span>123 456 7890</div>
    <div><span class="ico"><svg width="16" height="16" viewBox="0 0 16 16"><path d="M8 1a5 5 0 0 0-5 5c0 4 5 9 5 9s5-5 5-9a5 5 0 0 0-5-5z" fill="#b5121b"/><circle cx="8" cy="6" r="2" fill="#fff"/></svg></span>123 Lorem ipsum dolor sit</div>
    <div><span class="ico"><svg width="16" height="16" viewBox="0 0 16 16"><rect x="1" y="3" width="14" height="10" fill="#b5121b"/><path d="M1 3l7 6 7-6" stroke="#fff" stroke-width="1.4" fill="none"/></svg></span>info@lumakin.org</div>
  </div>
  <div class="copyright">© COPYRIGHTS 2021 LUMAKIN &nbsp;|&nbsp; ALL RIGHTS RESERVED</div>
</footer>

</body>
</html>
```